Social Media Graphics - Oakline Push REVISED

Create 6-7 individual social media graphics (square size) to encourage folks to join our online course called:

The Harvest Ledger Circle
How to Launch a Multi-Million Business From Scratch
Sign Up Today!

IMPORTANT: Make the largest and most prominent text on the graphic be: How to Launch a Multi-Million Business From Scratch

For the color scheme of the graphics, let's try a blue color palette; make sure the graphics appeal to both men and women

Make sure each graphic contains 1 of the 3 pics attached (crop pic as needed); and make sure one of the graphics is all TEXT only.

Target Market(s)

men and women looking to start a business

Industry/Entity Type

Entrepreneurship

Colors
0054AA
0677BA
7BADD7
CADEEF
E8F1F8

Requirements
Must have
• All the text and use the 3 pics provided; one graphic can be all text; Simple, modern design that's easy to read

```html
<!DOCTYPE html>
<html lang="en">
<head>
<meta charset="UTF-8">
<title>The Harvest Ledger Circle – Sign Up Today</title>
<link rel="stylesheet" href="https://fonts.googleapis.com/css2?family=Saira+Condensed:wght@600;700;800&display=swap">
<style>
  :root {
    --blue-deep: #0054AA;
    --blue-mid: #0677BA;
    --blue-soft: #7BADD7;
    --blue-pale: #CADEEF;
    --blue-mist: #E8F1F8;
  }
  * { margin: 0; padding: 0; box-sizing: border-box; }
  html, body {
    width: 1200px; height: 1200px; overflow: hidden;
    background: var(--blue-soft);
  }
  .graphic {
    position: relative;
    width: 1200px; height: 1200px;
    background: var(--blue-pale);
    border: 37px solid var(--blue-soft);
    font-family: "Saira Condensed", "Arial Narrow", sans-serif;
    text-transform: uppercase;
    overflow: hidden;
  }
  .badge-shapes { position: absolute; left: -37px; top: -37px; }
  .badge-word {
    position: absolute;
    color: var(--blue-mist);
    font-weight: 800;
    line-height: 1;
    display: flex; align-items: center; justify-content: center;
    white-space: nowrap;
  }
  .badge-pill-left { left: 257px; top: 255px; width: 166px; height: 78px; font-size: 50px; }
  .badge-pill-right { left: 702px; top: 255px; width: 166px; height: 78px; font-size: 48px; }
  .badge-core {
    left: 427px; top: 194px; width: 272px; height: 183px;
    font-size: 82px;
  }
  .badge-core span { display: block; transform: scaleY(2.1); }
  .badge-banner {
    position: absolute;
    left: 244px; top: 433px; width: 638px; height: 127px;
    background: var(--blue-mid);
    color: var(--blue-mist);
    font-weight: 800; font-size: 100px; letter-spacing: 4px;
    display: flex; align-items: center; justify-content: center;
    line-height: 1;
  }
  .headline {
    position: absolute;
    left: 0; right: 0; top: 574px;
    text-align: center;
    font-weight: 700;
    font-size: 103px;
    line-height: 106px;
    letter-spacing: 1px;
    white-space: nowrap;
  }
  .headline span { display: block; }
  .headline .tone-mid { color: var(--blue-mid); }
  .headline .tone-deep { color: var(--blue-deep); }
  .cta {
    position: absolute;
    left: 377px; top: 958px; width: 372px; height: 92px;
    background: var(--blue-deep);
    color: var(--blue-mist);
    font-weight: 700; font-size: 38px; letter-spacing: 0.5px;
    display: flex; align-items: center; justify-content: center;
  }
</style>
</head>
<body>
  <main class="graphic">
    <svg class="badge-shapes" width="1200" height="1200" viewBox="0 0 1200 1200" aria-hidden="true">
      <circle cx="600" cy="306" r="211" fill="var(--blue-soft)"/>
      <circle cx="600" cy="306" r="191" fill="var(--blue-deep)"/>
      <rect x="294" y="292" width="166" height="78" rx="39" fill="var(--blue-soft)"/>
      <rect x="739" y="292" width="166" height="78" rx="39" fill="var(--blue-soft)"/>
    </svg>
    <div class="badge-word badge-pill-left">The</div>
    <div class="badge-word badge-core"><span>Harvest</span></div>
    <div class="badge-word badge-pill-right">Ledger</div>
    <div class="badge-banner">Circle</div>

    <h1 class="headline">
      <span class="tone-mid">How to Launch a</span>
      <span class="tone-deep">Multi-Million Business</span>
      <span class="tone-mid">From Scratch</span>
    </h1>

    <div class="cta">Sign Up Today!</div>
  </main>
</body>
</html>
```